Brightline Energy Product Distribution Brochure

We are looking to have our current brochure for our customers completely redesigned...the idea is to present the relevant information in an attractive way . Our website is brightlineenergyco.example where you can find more information about us. We have included a file with a rough idea of the page order and what each should include but feel free to adapt based on design. The example provided is only for context and doesnt have to be maintained. We will be using the brochure both digitally and in print form. As long as it reads easily and is eye catching, the design can be horizontal or vertical.Final deliverable should be indesign file.

"Our Brands" page: should be limited to one page (space being enough) where it has the header for each one (for example diesel generators) space for one or two lines of text and then the corresponding logos for each of the five categories
Updates

For those asking: the "our brands" page should be a single page layout where there is a header with the corresponding section and space for maybe one line of text followed by the two logos for that category. Each of the product pages should be similar in fashion to the one in the document attached: a photo of the product with some white space and space for the text to be included. We will be posting additional examples today

Target Market(s)

We want to present it to customers both digitally and in print so they can see our products

Industry/Entity Type

Power Generation

Font styles to use
Serif

Requirements
Must have
• Eye catching and able to present the information in a presentable fashion. Rest is up to you.
Nice to have
• Should incorporate the colors of our logo but can also add other depending on design

```html
<!DOCTYPE html>
<html lang="en">
<head>
<meta charset="utf-8">
<title>Brightline Energy – Distributor Program Guide</title>
<link href="https://fonts.googleapis.com/css2?family=Montserrat:wght@400;500;600;700;900&display=swap" rel="stylesheet">
<style>
  :root {
    --backdrop: #a4a4a4;
    --paper: #f7f7f7;
    --paper-shade: #ececec;
    --yellow: #f6c31f;
    --yellow-deep: #e9b311;
    --ink: #2f2f2f;
    --ink-soft: #5a5a5a;
    --photo-dark: #2a2320;
    --photo-warm: #c9862a;
    --photo-glow: #f3c45a;
  }
  * { box-sizing: border-box; margin: 0; padding: 0; }
  html, body { width: 1200px; height: 717px; overflow: hidden; }
  body {
    background: var(--backdrop);
    font-family: "Montserrat", sans-serif;
    color: var(--ink);
    position: relative;
  }
  .spread {
    position: absolute;
    left: 120px; top: 48px;
    width: 960px; height: 620px;
    display: flex;
    box-shadow: 0 6px 18px rgba(0,0,0,.25);
  }
  .page {
    position: relative;
    width: 480px; height: 620px;
    background: var(--paper);
    overflow: hidden;
  }
  .page--back { background: linear-gradient(90deg, var(--paper) 85%, var(--paper-shade)); }
  .page--front { background: linear-gradient(90deg, var(--paper-shade), var(--paper) 12%); }
  .shapes { position: absolute; inset: 0; }

  .photo {
    position: absolute;
    left: 0; width: 480px;
    background:
      radial-gradient(ellipse at 30% 60%, rgba(243,196,90,.75), transparent 45%),
      radial-gradient(ellipse at 75% 40%, rgba(201,134,42,.6), transparent 50%),
      linear-gradient(180deg, var(--photo-warm) 0%, var(--photo-dark) 55%, #4a3524 100%);
  }
  .page--back .photo { top: 225px; height: 245px; }
  .page--front .photo {
    top: 135px; height: 285px;
    background:
      radial-gradient(ellipse at 35% 55%, rgba(243,196,90,.6), transparent 40%),
      radial-gradient(ellipse at 80% 30%, rgba(201,134,42,.55), transparent 45%),
      linear-gradient(180deg, #6a4a2e 0%, var(--photo-dark) 50%, #5a3a22 100%);
  }

  .intro { position: absolute; left: 42px; top: 74px; width: 380px; }
  .intro__heading { font-size: 22px; font-weight: 700; letter-spacing: .5px; }
  .rule { display: block; width: 42px; height: 3px; background: var(--yellow); margin: 8px 0 10px; }
  .intro__body { font-size: 8px; line-height: 1.45; color: var(--ink-soft); }

  .brand {
    position: absolute;
    display: flex; align-items: center; gap: 9px;
    font-weight: 600; color: var(--ink);
    white-space: nowrap;
  }
  .brand__square { width: 26px; height: 26px; background: var(--yellow); }
  .page--back .brand {
    left: 34px; top: 505px; font-size: 14px;
    flex-direction: column; align-items: center; gap: 8px;
  }
  .page--back .brand__square { width: 30px; height: 30px; }
  .page--front .brand { left: 235px; top: 520px; font-size: 20px; }
  .page--front .brand__square { width: 32px; height: 32px; }

  .contact {
    position: absolute; left: 190px; top: 500px;
    font-size: 9px; line-height: 1.45; color: var(--ink-soft);
    font-style: normal; white-space: nowrap;
  }
  .contact__phone { font-weight: 700; color: var(--ink); font-size: 10px; margin-top: 5px; }
  .contact__web { font-weight: 700; color: var(--yellow-deep); font-size: 9px; margin-top: 4px; }

  .cover-title { position: absolute; left: 34px; top: 36px; }
  .cover-title__main { font-size: 21px; font-weight: 900; line-height: 1.05; letter-spacing: .3px; color: var(--ink); }
  .cover-title .rule { width: 60px; height: 2px; margin: 10px 0 10px; }
  .cover-title__sub { font-size: 12px; font-weight: 600; line-height: 1.2; letter-spacing: .6px; color: var(--ink); }

  .hotline { position: absolute; left: 0; top: 522px; width: 170px; text-align: center; }
  .hotline__phone { font-size: 12px; font-weight: 700; color: var(--ink); letter-spacing: .3px; }
  .hotline__web { font-size: 8px; font-weight: 500; color: var(--ink); margin-top: 12px; }
</style>
</head>
<body>
  <main class="spread">
    <section class="page page--back">
      <div class="photo" role="img" aria-label="Industrial power plant at dusk with steam rising and warm lights"></div>
      <svg class="shapes" width="480" height="620" aria-hidden="true">
        <polygon points="360,470 480,470 480,620 425,620" fill="var(--yellow)"/>
      </svg>
      <div class="intro">
        <h2 class="intro__heading">LOREM IPSUM</h2>
        <span class="rule"></span>
        <p class="intro__body">Lorem ipsum dolor sit amet, consectetuer adipiscing elit, sed diam nonummy nibh euismod tincidunt ut laoreet dolore magna aliquam erat volutpat. Ut wisi enim ad minim veniam, quis nostrud exerci tation ullamcorper suscipit lobortis nisl ut aliquip ex ea commodo consequat. Duis autem vel eum iriure dolor in hendrerit in vulputate velit esse molestie consequat.</p>
      </div>
      <div class="brand"><span class="brand__square"></span>Brightline Energy</div>
      <address class="contact">
        Brightline Energy Limited, Inc.<br>
        4410 Harbor Ridge Road<br>
        Lakemont, FL 30000, USA
        <div class="contact__phone">1-800-555-0142</div>
        <div class="contact__web">brightlineenergyco.example</div>
      </address>
    </section>

    <section class="page page--front">
      <svg class="shapes" width="480" height="620" aria-hidden="true">
        <polygon points="345,0 480,0 480,135 340,135" fill="var(--yellow)"/>
        <polygon points="0,420 172,420 165,620 0,620" fill="var(--yellow)"/>
      </svg>
      <div class="photo" role="img" aria-label="Steel works and power station lit up at night"></div>
      <header class="cover-title">
        <h1 class="cover-title__main">DISTRIBUTOR<br>PROGRAM GUIDE</h1>
        <span class="rule"></span>
        <p class="cover-title__sub">DIESEL GENERATORS<br>ALTERNATORS &amp; PARTS</p>
      </header>
      <div class="hotline">
        <div class="hotline__phone">1-800-555-0142</div>
        <div class="hotline__web">brightlineenergyco.example</div>
      </div>
      <div class="brand"><span class="brand__square"></span>Brightline Energy</div>
    </section>
  </main>
</body>
</html>
```